Brindle Sky Port needs a new upscale business card design for our high end aircraft hangar complex

Brindle Sky Port (BSP) is a large, upscale jet hangar complex in the US housing expensive aircraft. We need a new business card design, using our current logo. We will be attending a industry convention and need a card design that will stand out and be remembered by aircraft owners and private pilots.

Target Market(s)

Aircraft pilots or owners looking for a new upscale hangar

Industry/Entity Type

Airport

Contact Information for Business Card

I like to use very heavy card stock, 400#, double sided. Square, no rounded edges please.

Colors
3276b5
0255a3
85abd2

Requirements
Must have
• An expensive, classy design, vivid colors.
Nice to have
• Needs to look very expensive and classy, and have some "pop". Designer must be able to download or copy my current typeface or fonts.
• One card side might be black with the "Logo and Brindle Sky Port Double line image in blue (or try gold, or glossy black), and perhaps have a grayed out "K720 jet silhouette". The other card side would have our contact info, and perhaps the "BSP Logo only". I'd like my contact info 'stacked', not in a paragraph format.
Should not have
• Should not look "too busy". Having a double-sided card will help.

```html
<!DOCTYPE html>
<html lang="en">
<head>
<meta charset="utf-8">
<title>Brindle Sky Port – Business Card</title>
<link rel="stylesheet" href="https://fonts.googleapis.com/css2?family=Montserrat:wght@700;800&family=Roboto:wght@400;500&display=swap">
<style>
  :root {
    --bg: #e9e6e1;
    --blue-deep: #0255a3;
    --blue: #3276b5;
    --blue-light: #85abd2;
    --card-blue-top: #2f7fbf;
    --card-blue-bottom: #1a5f9c;
    --card-dark: #3a3b3e;
    --card-dark-edge: #2a2b2d;
    --white: #ffffff;
  }
  html, body {
    margin: 0;
    padding: 0;
    width: 1200px;
    height: 1023px;
    overflow: hidden;
    background: var(--bg);
  }
  .canvas {
    position: relative;
    width: 1200px;
    height: 1023px;
  }
  .card {
    position: absolute;
    width: 600px;
    height: 343px;
    border-radius: 0;
    overflow: hidden;
    box-shadow: 0 18px 40px rgba(0,0,0,0.28);
  }
  /* Front: contact side */
  .card--front {
    left: 70px;
    top: 110px;
    background: radial-gradient(ellipse at 55% 55%, #3b95cf 0%, var(--card-blue-top) 40%, var(--card-blue-bottom) 100%);
    color: var(--white);
  }
  .front-photo {
    position: absolute;
    right: 0;
    top: 0;
    width: 330px;
    height: 343px;
    background: radial-gradient(ellipse at 50% 45%, rgba(20,70,120,0.35) 0%, rgba(20,70,120,0.12) 50%, rgba(20,70,120,0) 75%);
  }
  .brand {
    position: absolute;
    left: 42px;
    top: 190px;
    display: flex;
    align-items: center;
    gap: 12px;
  }
  .brand__mark {
    width: 18px;
    height: 18px;
    background: var(--white);
  }
  .brand__name {
    font-family: "Montserrat", sans-serif;
    font-weight: 800;
    font-size: 26px;
    line-height: 1.05;
    letter-spacing: 0.5px;
    text-transform: uppercase;
  }
  .person {
    position: absolute;
    right: 50px;
    top: 40px;
    text-align: right;
    font-family: "Roboto", sans-serif;
  }
  .person__name {
    font-weight: 500;
    font-size: 26px;
    margin: 0;
  }
  .person__title {
    font-size: 15px;
    margin: 2px 0 0;
  }
  .contacts {
    position: absolute;
    left: 270px;
    bottom: 38px;
    list-style: none;
    margin: 0;
    padding: 0;
    font-family: "Roboto", sans-serif;
    font-size: 16px;
  }
  .contacts li {
    display: flex;
    align-items: center;
    gap: 9px;
    margin-top: 6px;
  }
  .contacts svg {
    width: 13px;
    height: 13px;
    flex: none;
  }
  /* Back: logo side */
  .card--back {
    left: 530px;
    top: 570px;
    background: linear-gradient(160deg, #46474a 0%, var(--card-dark) 55%, var(--card-dark-edge) 100%);
  }
  .back-photo {
    position: absolute;
    left: 70px;
    top: 40px;
    width: 300px;
    height: 260px;
    background: radial-gradient(ellipse at 50% 50%, rgba(15,15,16,0.75) 0%, rgba(30,30,32,0.35) 35%, rgba(58,59,62,0) 70%);
  }
  .back-brand {
    position: absolute;
    right: 60px;
    top: 118px;
    display: flex;
    align-items: center;
    gap: 16px;
  }
  .back-brand__mark {
    width: 26px;
    height: 26px;
    border-radius: 50%;
    background: var(--blue);
  }
  .back-brand__name {
    font-family: "Montserrat", sans-serif;
    font-weight: 800;
    font-size: 92px;
    line-height: 1;
    color: var(--blue);
    letter-spacing: 4px;
  }
</style>
</head>
<body>
<main class="canvas">

  <section class="card card--front" aria-label="Business card, contact side">
    <div class="front-photo" role="img" aria-label="Faded photo of a private jet nose and engine in blue tones"></div>

    <div class="brand">
      <span class="brand__mark"></span>
      <span class="brand__name">Brindle<br>Sky Port</span>
    </div>

    <div class="person">
      <p class="person__name">Your Name</p>
      <p class="person__title">Title</p>
    </div>

    <ul class="contacts">
      <li>
        <svg viewBox="0 0 16 16" aria-hidden="true"><path fill="#fff" d="M3.6 1.2 6 3.6 4.8 5.6c.9 2 2.6 3.7 4.6 4.6l2-1.2 2.4 2.4-1.4 2.4C7.3 13.6 2.4 8.7 1.2 3z"/></svg>
        88-123-54321
      </li>
      <li>
        <svg viewBox="0 0 16 16" aria-hidden="true"><rect x="1.5" y="3.5" width="13" height="9" fill="none" stroke="#fff" stroke-width="1.3"/><path d="M1.5 3.5 8 9l6.5-5.5" fill="none" stroke="#fff" stroke-width="1.3"/></svg>
        info@yourweb.com
      </li>
      <li>
        <svg viewBox="0 0 16 16" aria-hidden="true"><circle cx="8" cy="8" r="6.5" fill="none" stroke="#fff" stroke-width="1.3"/><path d="M1.5 8h13M8 1.5c-3 3.5-3 9.5 0 13M8 1.5c3 3.5 3 9.5 0 13" fill="none" stroke="#fff" stroke-width="1.1"/></svg>
        www.yourweb.com
      </li>
    </ul>
  </section>

  <section class="card card--back" aria-label="Business card, logo side">
    <div class="back-photo" role="img" aria-label="Grayed-out front view silhouette of a private jet"></div>
    <div class="back-brand">
      <span class="back-brand__mark"></span>
      <span class="back-brand__name">BSP</span>
    </div>
  </section>

</main>
</body>
</html>
```